Report template for evaluation reports to be used by non designers

We are looking for a report template that meets all the requirements listed in the attached documents. letter head, logo etc have been enclosed. Its important that the colour integrity is kept, but beyond that options are welcome.
Its important that the document is extremely easy to use and that is able to be adapted to include eatables, figures, pictures, text boxes etc and keep the integrity of the template

Target Market(s)

Governments, Civil society organisations and research institutions

Font styles to use
Sans Serif

Colors
6b449b
876aae
c0c0c0
000000

Requirements
Must have
• Clean, professional, not concluded, modern, must be easy to use
Should not have
• too busy, hard to use

```html
<!DOCTYPE html>
<html lang="en">
<head>
<meta charset="utf-8">
<title>Civic Insight Institute – Report Covers</title>
<link rel="stylesheet" href="https://fonts.googleapis.com/css2?family=Open+Sans:wght@400;600;700&display=swap">
<style>
  :root {
    --purple: #6b449b;
    --lavender: #876aae;
    --title: #6a55a8;
    --silver: #c0c0c0;
    --ink: #000000;
    --text: #2a2a2a;
    --paper: #f6f6f8;
    --backdrop: #a9a9ab;
  }
  * { box-sizing: border-box; margin: 0; padding: 0; }
  html, body { width: 1200px; height: 925px; overflow: hidden; }
  body {
    background: var(--backdrop);
    font-family: "Open Sans", Arial, sans-serif;
    color: var(--text);
    position: relative;
  }
  .spread {
    position: absolute;
    left: 34px; top: 62px;
    display: flex;
    gap: 0;
    box-shadow: 0 14px 40px rgba(0,0,0,.25);
  }
  .page {
    position: relative;
    width: 566px; height: 800px;
    background: var(--paper);
    overflow: hidden;
  }
  .page + .page { border-left: 1px solid #dcdce2; }

  .wordmark {
    font-weight: 400;
    color: var(--ink);
    letter-spacing: .18em;
    line-height: 1.1;
    display: flex;
    align-items: center;
    gap: 12px;
  }
  .wordmark .dot {
    width: 22px; height: 22px; border-radius: 50%;
    background: var(--lavender);
    flex: none;
  }
  .wordmark .name { font-size: 30px; }
  .wordmark .sub { display: block; font-size: 11px; letter-spacing: .32em; margin-top: 4px; }

  /* back cover */
  .back .rule-top {
    position: absolute; left: 70px; top: 0;
    width: 1.5px; height: 330px; background: var(--purple);
  }
  .back .wordmark { position: absolute; left: 70px; top: 380px; }
  .back .rule-mid {
    position: absolute; left: 70px; top: 490px;
    width: 1.5px; height: 70px; background: var(--purple);
  }
  .contact {
    position: absolute; left: 70px; top: 585px;
    display: grid; grid-template-columns: 70px auto; row-gap: 10px;
    font-size: 15px;
  }
  .contact dt, .meta dt { color: var(--purple); font-weight: 600; }
  .contact dd { color: var(--ink); }
  .back .rule-low {
    position: absolute; left: 70px; top: 660px;
    width: 1.5px; height: 50px; background: var(--purple);
  }

  /* front cover */
  .front .wordmark { position: absolute; left: 48px; top: 48px; }
  .title {
    position: absolute; left: 48px; top: 180px; width: 460px;
    font-size: 32px; font-weight: 700; line-height: 1.18;
    color: var(--title);
  }
  .front .rule-above {
    position: absolute; left: 48px; top: 168px;
    width: 470px; height: 1.5px; background: var(--lavender);
  }
  .front .rule-below {
    position: absolute; left: 48px; top: 318px;
    width: 470px; height: 1.5px; background: var(--lavender);
  }
  .client {
    position: absolute; left: 48px; top: 352px;
    display: grid; grid-template-columns: 80px auto; font-size: 13px;
  }
  .client dt { color: var(--purple); font-weight: 600; }
  .client-name {
    position: absolute; left: 128px; top: 395px;
    display: flex; align-items: center; gap: 10px;
    font-size: 22px; font-weight: 700; color: var(--ink);
  }
  .client-name .mark { width: 18px; height: 18px; border-radius: 50%; background: var(--ink); }
  .front .rule-dashed {
    position: absolute; left: 128px; top: 462px;
    width: 300px; border-top: 1.5px dashed var(--lavender);
  }
  .meta {
    position: absolute; left: 48px; top: 560px;
    display: grid; grid-template-columns: 80px auto; row-gap: 14px;
    font-size: 14px;
  }
  .meta dd { color: var(--ink); }

  .foot { position: absolute; left: 0; bottom: 0; width: 566px; height: 110px; }
  .foot .pill {
    position: absolute; left: 50%; top: 36px; transform: translateX(-50%);
    border: 2px solid var(--purple); border-radius: 14px;
    padding: 2px 14px; background: var(--paper);
    font-size: 10px; font-weight: 700; color: var(--ink);
  }
</style>
</head>
<body>
  <main class="spread">
    <section class="page back" aria-label="Back cover">
      <span class="rule-top"></span>
      <div class="wordmark">
        <span class="dot"></span>
        <span><span class="name">CIVIC INSIGHT</span><span class="sub">RESEARCH INSTITUTE</span></span>
      </div>
      <span class="rule-mid"></span>
      <dl class="contact">
        <dt>Email:</dt><dd>info@civicinsight.org</dd>
        <dt>ISBN:</dt><dd>CHF-467.113.214</dd>
      </dl>
      <span class="rule-low"></span>
      <div class="foot">
        <svg width="566" height="110" viewBox="0 0 566 110" aria-hidden="true">
          <path d="M0 80 Q283 30 566 0" fill="none" stroke="var(--purple)" stroke-width="2"/>
        </svg>
        <span class="pill" style="top:40px">www.civicinsight.org</span>
      </div>
    </section>

    <section class="page front" aria-label="Front cover">
      <div class="wordmark">
        <span class="dot"></span>
        <span><span class="name">CIVIC INSIGHT</span><span class="sub">RESEARCH INSTITUTE</span></span>
      </div>
      <span class="rule-above"></span>
      <h1 class="title">Pre-Study for an Impact Evaluation of the ABC programme</h1>
      <span class="rule-below"></span>
      <dl class="client">
        <dt>Client:</dt><dd>Northfield Trust</dd>
      </dl>
      <div class="client-name"><span class="mark"></span>NORTHFIELD TRUST</div>
      <span class="rule-dashed"></span>
      <dl class="meta">
        <dt>Date:</dt><dd>September 22, 2018</dd>
        <dt>Author:</dt><dd>Mira T. Holloway, Ph.D</dd>
      </dl>
      <div class="foot">
        <svg width="566" height="110" viewBox="0 0 566 110" aria-hidden="true">
          <path d="M0 80 Q283 30 566 0" fill="none" stroke="var(--purple)" stroke-width="2"/>
        </svg>
        <span class="pill" style="top:40px">www.civicinsight.org</span>
      </div>
    </section>
  </main>
</body>
</html>
```